Company director needs a business card design

I am a semi-retired former senior finance executive who sits on a number of public and private company boards and do some consulting work. I work largely with emerging businesses but deal regularly with top end of town lawyers, bankers etc. I need a thoughtful but relatively conservative design which would also resonate with my younger client base. Some colour would be good. Information limited to name, address, office tel, mobile and email.

Finance

```html
<!DOCTYPE html>
<html lang="en">
<head>
<meta charset="utf-8">
<title>Daniel Harrow – Business Card</title>
<link rel="stylesheet" href="https://fonts.googleapis.com/css2?family=Tinos&family=Caladea:wght@400;700&display=swap">
<style>
  :root {
    --page-bg: #e9e7e2;
    --card-bg: #dcefed;
    --card-edge: #c6dbd8;
    --ink: #1c1c1c;
    --rule: #2a2a2a;
  }
  html, body {
    margin: 0;
    width: 1200px;
    height: 800px;
    overflow: hidden;
    background: var(--page-bg);
  }
  .business-card {
    position: absolute;
    left: 100px;
    top: 130px;
    width: 1000px;
    height: 540px;
    background: var(--card-bg);
    border: 1px solid var(--card-edge);
    box-shadow: 0 6px 18px rgba(0,0,0,0.12);
    color: var(--ink);
  }
  .identity {
    position: absolute;
    left: 100px;
    top: 250px;
    width: 270px;
    font-family: "Tinos", "Times New Roman", serif;
  }
  .identity__name {
    margin: 0;
    font-size: 40px;
    font-weight: 400;
    letter-spacing: -0.5px;
    line-height: 1;
    white-space: nowrap;
  }
  .identity__role {
    margin: 4px 0 0;
    font-size: 24px;
    line-height: 1;
  }
  .divider {
    position: absolute;
    left: 388px;
    top: 40px;
    width: 3px;
    height: 460px;
    background: var(--rule);
  }
  .contact-list {
    position: absolute;
    left: 480px;
    top: 66px;
    margin: 0;
    padding: 0;
    list-style: none;
    font-family: "Caladea", "Cambria", serif;
    font-size: 27px;
    line-height: 1.2;
    letter-spacing: 0.8px;
  }
  .contact-list__item {
    display: flex;
    align-items: flex-start;
    margin-bottom: 8px;
  }
  .contact-list__item--address { margin-bottom: 22px; }
  .contact-list__item--email { font-weight: 700; }
  .contact-list__icon {
    width: 24px;
    height: 28px;
    flex: none;
    margin-right: 70px;
    margin-top: 3px;
    fill: var(--ink);
  }
</style>
</head>
<body>
  <section class="business-card" aria-label="Business card">
    <div class="identity">
      <h1 class="identity__name">Daniel Harrow</h1>
      <p class="identity__role">Project Manager</p>
    </div>
    <div class="divider"></div>
    <ul class="contact-list">
      <li class="contact-list__item">
        <svg class="contact-list__icon" viewBox="0 0 24 24" aria-hidden="true"><path d="M6.6 10.8a15.1 15.1 0 0 0 6.6 6.6l2.2-2.2c.3-.3.7-.4 1-.2 1.1.4 2.3.6 3.6.6.6 0 1 .4 1 1V20c0 .6-.4 1-1 1C10.6 21 3 13.4 3 4c0-.6.4-1 1-1h3.5c.6 0 1 .4 1 1 0 1.3.2 2.5.6 3.6.1.3 0 .7-.2 1z"/></svg>
        <span>+1 (555) 0142 377</span>
      </li>
      <li class="contact-list__item">
        <svg class="contact-list__icon" viewBox="0 0 24 24" aria-hidden="true"><path d="M7 2h10a2 2 0 0 1 2 2v16a2 2 0 0 1-2 2H7a2 2 0 0 1-2-2V4a2 2 0 0 1 2-2zm0 2v14h10V4zm5 15.2a.9.9 0 1 0 0 1.8.9.9 0 0 0 0-1.8z"/></svg>
        <span>+1 (555) 0198 264</span>
      </li>
      <li class="contact-list__item contact-list__item--address">
        <svg class="contact-list__icon" viewBox="0 0 24 24" aria-hidden="true"><path d="M12 2a7 7 0 0 0-7 7c0 5.2 7 13 7 13s7-7.8 7-13a7 7 0 0 0-7-7z"/></svg>
        <span>48 Elm Court, Riverton,<br>NY 10044<br>P.O. Box: 570826</span>
      </li>
      <li class="contact-list__item contact-list__item--email">
        <svg class="contact-list__icon" viewBox="0 0 24 24" aria-hidden="true"><path d="M3 6h18v12H3zm1.6 1.2L12 12.6l7.4-5.4zM4.5 16.8h15V8.6L12 14.1 4.5 8.6z"/></svg>
        <span>info@harrowboards.example</span>
      </li>
    </ul>
  </section>
</body>
</html>
```